Business card for medical clinic

I need an upmarket, modern medical/health business card for my clinic

Contact Information for Business Card

name, address, email, qr code

```html
<!DOCTYPE html>
<html lang="en">
<head>
<meta charset="utf-8">
<title>Solara Health Group – Business Card</title>
<link rel="stylesheet" href="https://fonts.googleapis.com/css2?family=Montserrat:wght@400;500;700&display=swap">
<style>
  :root {
    --navy: #253a5c;
    --steel: #2f5f86;
    --sky: #2ea3d8;
    --ink: #1f2a3a;
    --paper: #ffffff;
    --backdrop: #2b2d31;
  }
  * { margin: 0; padding: 0; box-sizing: border-box; }
  html, body { width: 1200px; height: 900px; overflow: hidden; }
  body {
    background: var(--backdrop);
    font-family: "Montserrat", sans-serif;
    position: relative;
  }
  .card {
    position: absolute;
    left: 320px;
    width: 560px;
    height: 320px;
    overflow: hidden;
  }
  .card--front {
    top: 90px;
    background: linear-gradient(135deg, var(--navy) 0%, var(--steel) 55%, var(--sky) 100%);
    display: flex;
    align-items: center;
    justify-content: center;
  }
  .card--back {
    top: 490px;
    background: var(--paper);
  }
  .brand {
    display: flex;
    align-items: center;
    gap: 14px;
    font-weight: 500;
    letter-spacing: 0.12em;
    text-transform: uppercase;
  }
  .brand__dot {
    width: 22px; height: 22px; border-radius: 50%;
  }
  .card--front .brand { color: var(--paper); font-size: 26px; }
  .card--front .brand__dot { border: 3px solid var(--paper); }
  .card--back .brand {
    position: absolute; left: 40px; top: 70px;
    color: var(--steel); font-size: 22px;
  }
  .card--back .brand__dot { border: 3px solid var(--steel); }
  .holder {
    position: absolute; right: 300px; top: 150px;
    text-align: right;
  }
  .holder__name { color: var(--sky); font-weight: 700; font-size: 20px; }
  .holder__role { color: var(--ink); font-size: 11px; margin-top: 2px; }
  .divider {
    position: absolute; left: 280px; top: 138px;
    width: 1px; height: 64px; background: var(--sky);
  }
  .contacts {
    position: absolute; left: 296px; top: 136px;
    list-style: none;
    font-size: 11px; color: var(--ink);
  }
  .contacts li { display: flex; align-items: center; gap: 8px; height: 22px; }
  .contacts svg { width: 12px; height: 12px; fill: var(--sky); flex: none; }
  .address-band {
    position: absolute; left: 0; right: 0; top: 248px; height: 46px;
    background: linear-gradient(90deg, var(--navy), var(--steel) 60%, var(--sky));
    color: var(--paper);
    font-size: 13px;
    display: flex; align-items: center; justify-content: center;
    letter-spacing: 0.02em;
  }
</style>
</head>
<body>
  <section class="card card--front" aria-label="Card front">
    <div class="brand"><span class="brand__dot"></span>Solara Health Group</div>
  </section>

  <section class="card card--back" aria-label="Card back">
    <div class="brand"><span class="brand__dot"></span>Solara Health Group</div>

    <div class="holder">
      <p class="holder__name">Daniel Reyes</p>
      <p class="holder__role">Managing Director</p>
    </div>

    <div class="divider"></div>

    <ul class="contacts">
      <li>
        <svg viewBox="0 0 24 24" aria-hidden="true"><path d="M6.6 10.8a15.1 15.1 0 0 0 6.6 6.6l2.2-2.2c.3-.3.7-.4 1-.2 1.1.4 2.3.6 3.6.6.6 0 1 .4 1 1V20c0 .6-.4 1-1 1A17 17 0 0 1 3 4c0-.6.4-1 1-1h3.5c.6 0 1 .4 1 1 0 1.3.2 2.5.6 3.6.1.3 0 .7-.2 1z"/></svg>
        555.310.2047
      </li>
      <li>
        <svg viewBox="0 0 24 24" aria-hidden="true"><path d="M2 5h20v14H2zm2 2v.5l8 5 8-5V7l-8 5z"/></svg>
        hello@solarahealth.com
      </li>
      <li>
        <svg viewBox="0 0 24 24" aria-hidden="true"><path d="M12 2a10 10 0 1 0 0 20 10 10 0 0 0 0-20zm6.9 9h-3a15 15 0 0 0-1.3-5.6A8 8 0 0 1 18.9 11zM12 4c.9 1.3 1.7 3.8 1.9 7h-3.8c.2-3.2 1-5.7 1.9-7zM9.4 5.4A15 15 0 0 0 8.1 11h-3a8 8 0 0 1 4.3-5.6zM5.1 13h3a15 15 0 0 0 1.3 5.6A8 8 0 0 1 5.1 13zm6.9 7c-.9-1.3-1.7-3.8-1.9-7h3.8c-.2 3.2-1 5.7-1.9 7zm2.6-1.4a15 15 0 0 0 1.3-5.6h3a8 8 0 0 1-4.3 5.6z"/></svg>
        www.solarahealth.com
      </li>
    </ul>

    <div class="address-band">48 Cedar Ridge Lane Fairview, TN 37062</div>
  </section>
</body>
</html>
```